Website Design for Hulls for Heroes

Please design and code a new website.
Here are the sites I like best:
http://www.sailbrisk.com/alternate/
http://www.wheelsforhonor.org
Please make it similar. This is NOT a car donation site. It's a boat donation site. I just like this sites above as a lead generation sites.
Old site:
http://hullsforheroes.org
Updates
Coding
Coded - Design and coding required
Number of Pages Required
1 page
Look and feel
Each slider illustrates characteristics of the customer's brand and the style your logo design should communicate.

```html
<!DOCTYPE html>
<html lang="en">
<head>
<meta charset="utf-8">
<title>Hulls for Heroes – Donate Your Boat</title>
<link href="https://fonts.googleapis.com/css2?family=Montserrat:wght@400;600;700;800&family=Open+Sans:wght@400;600;700&family=Oswald:wght@500;700&display=swap" rel="stylesheet">
<style>
:root{
  --navy:#0d2552;
  --navy-deep:#081a3d;
  --blue:#173e86;
  --blue-mid:#1f4f9e;
  --red:#c8202f;
  --red-dark:#a3161f;
  --white:#ffffff;
  --ink:#1d2433;
  --muted:#5d6678;
  --line:#d9dee8;
  --paper:#f3f5f9;
}
*{box-sizing:border-box;margin:0;padding:0}
html,body{width:1200px;height:2952px;overflow:hidden}
body{font-family:"Open Sans",Arial,sans-serif;color:var(--ink);background:var(--white);position:relative}
.brand-name{font-family:"Montserrat",Arial,sans-serif;font-weight:800;text-transform:uppercase;letter-spacing:1px;color:var(--white)}
/* header */
.site-header{position:absolute;top:0;left:0;width:1200px;height:150px;background:linear-gradient(180deg,var(--navy-deep),var(--navy))}
.site-header .logo{position:absolute;left:60px;top:50px;display:flex;align-items:center;gap:14px}
.site-header .logo .dot{width:38px;height:38px;border-radius:50%;background:var(--red)}
.site-header .logo .brand-name{font-size:34px}
.call-box{display:flex;align-items:center;gap:16px;color:var(--white)}
.site-header .call-box{position:absolute;right:60px;top:36px}
.call-box .icon{flex:none;width:64px;height:64px;border:3px solid var(--white);border-radius:50%;display:flex;align-items:center;justify-content:center}
.call-box .label{font-family:"Montserrat",sans-serif;font-weight:700;font-size:18px;text-transform:uppercase}
.call-box .phone{font-family:"Montserrat",sans-serif;font-weight:800;font-size:38px;line-height:1.05;white-space:nowrap}
.call-box .hours{font-size:13px;opacity:.85}
.main-nav{position:absolute;top:150px;left:0;width:1200px;height:46px;background:var(--blue)}
.main-nav ul{list-style:none;display:flex;gap:44px;padding-left:170px;height:46px;align-items:center}
.main-nav a{color:var(--white);text-decoration:none;font-family:"Montserrat",sans-serif;font-weight:700;font-size:14px;text-transform:uppercase}
.main-nav .nav-cta{position:absolute;right:0;top:0;height:46px;width:360px;background:var(--red);color:var(--white);display:flex;align-items:center;justify-content:center;font-family:"Montserrat",sans-serif;font-weight:700;font-size:17px;text-transform:uppercase}
/* hero */
.hero{position:absolute;top:196px;left:0;width:1200px;height:404px}
.hero .photo{position:absolute;inset:0;background:linear-gradient(110deg,#9fb5c9 0%,#dfe6ec 35%,#6f7a66 55%,#3b4532 75%,#b8c6d4 100%)}
.donate-form{position:absolute;right:40px;top:18px;width:360px;background:var(--white);border:1px solid var(--line);padding:14px 16px;box-shadow:0 6px 20px rgba(0,0,0,.2)}
.donate-form h2{font-family:"Montserrat",sans-serif;font-size:15px;font-weight:700;text-align:center;color:var(--navy);margin-bottom:10px}
.form-row{display:flex;gap:8px;margin-bottom:7px}
.field{flex:1;height:28px;border:1px solid var(--line);font-size:12px;color:var(--muted);padding:0 8px;display:flex;align-items:center;justify-content:space-between;background:var(--white)}
.btn-donate{display:inline-block;margin-top:6px;background:var(--red);color:var(--white);font-family:"Montserrat",sans-serif;font-weight:700;font-size:14px;padding:9px 26px;text-transform:uppercase}
/* banner */
.banner{position:absolute;top:600px;left:0;width:1200px;height:210px;background:linear-gradient(100deg,var(--red-dark) 0%,var(--red) 22%,var(--navy) 48%,var(--blue) 100%)}
.banner .headline{position:absolute;left:60px;top:34px;color:var(--white);text-transform:uppercase}
.banner .headline .l1,.banner .headline .l3{font-family:"Montserrat",sans-serif;font-weight:700;font-size:30px;display:block}
.banner .headline .l2{font-family:"Oswald",sans-serif;font-weight:700;font-size:76px;line-height:1;display:block;letter-spacing:2px}
.perks{position:absolute;right:50px;top:50px;display:flex;gap:40px}
.perk{width:110px;text-align:center;color:var(--white);font-size:12px;line-height:1.35}
.perk .ring{width:56px;height:56px;border:2px solid var(--white);border-radius:50%;margin:0 auto 10px;display:flex;align-items:center;justify-content:center}
/* how to donate */
.section-title{font-family:"Montserrat",sans-serif;font-weight:800;font-size:32px;text-transform:uppercase;text-align:center}
.section-title .accent{color:var(--red)}
.how{position:absolute;top:810px;left:0;width:1200px;height:390px;background:var(--white)}
.how .section-title{color:var(--navy);margin-top:60px}
.how .rule{width:80px;height:3px;background:var(--red);margin:12px auto 0}
.steps{display:flex;justify-content:space-between;padding:60px 80px 0}
.step{width:320px;display:flex;gap:16px}
.step .icon{flex:none;width:54px;height:54px}
.step h3{font-family:"Montserrat",sans-serif;font-weight:700;font-size:15px;color:var(--navy);text-transform:uppercase;margin-bottom:8px;line-height:1.3}
.step p{font-size:13px;color:var(--muted);line-height:1.55}
/* why */
.why{position:absolute;top:1200px;left:0;width:1200px;height:630px;background:linear-gradient(180deg,var(--navy-deep),var(--blue-mid) 50%,var(--navy))}
.why .section-title{color:var(--white);margin-top:54px}
.why .ring-wrap{position:absolute;left:390px;top:130px;width:420px;height:420px}
.why .center-name{position:absolute;left:390px;top:320px;width:420px;text-align:center;font-size:24px}
.feature{position:absolute;width:330px;color:var(--white);font-size:13px;line-height:1.5}
.feature h3{font-family:"Montserrat",sans-serif;font-weight:700;font-size:15px;margin-bottom:4px}
.feature.left{text-align:right}
/* faq */
.faq{position:absolute;top:1830px;left:0;width:1200px;height:620px;background:var(--white)}
.faq .section-title{color:var(--navy);margin-top:50px}
.faq-list{position:absolute;left:80px;top:140px;width:560px}
.faq-item{border-bottom:1px solid var(--line);padding:13px 4px;display:flex;justify-content:space-between;font-family:"Montserrat",sans-serif;font-weight:600;font-size:14px;color:var(--navy)}
.faq-item.open{display:block}
.faq-item.open p{font-family:"Open Sans",sans-serif;font-weight:400;font-size:12.5px;color:var(--muted);line-height:1.55;margin-top:8px}
.faq-item .q{display:flex;justify-content:space-between}
.faq .photo{position:absolute;left:680px;top:140px;width:440px;height:420px;background:linear-gradient(160deg,#e7c9a1,#b98a5c 45%,#6e4b34 80%,#3b2a20)}
/* footer */
.site-footer{position:absolute;top:2450px;left:0;width:1200px;height:462px;background:linear-gradient(180deg,var(--blue),var(--navy-deep))}
.footer-brand{position:absolute;left:0;top:40px;width:1200px;text-align:center}
.footer-brand .brand-name{font-size:40px}
.footer-cols{position:absolute;left:60px;top:170px;display:flex;gap:40px}
.footer-col{color:var(--white);font-size:13px;line-height:1.6}
.footer-col h4{font-family:"Montserrat",sans-serif;font-weight:700;font-size:15px;text-transform:uppercase;margin-bottom:12px}
.footer-col ul{list-style:none}
.badge{width:150px;height:44px;background:#e8ecf3;border-radius:4px;margin-bottom:10px}
.badge.round{width:54px;height:54px;border-radius:50%}
.footer-call{position:absolute;right:60px;top:190px;width:410px;border:2px solid var(--white);padding:22px 24px}
.footer-call .phone{font-size:34px}
.copyright{position:absolute;top:2912px;left:0;width:1200px;height:40px;background:var(--red);color:var(--white);font-size:12px;font-weight:600;display:flex;align-items:center;justify-content:center;text-transform:uppercase;letter-spacing:.5px}
</style>
</head>
<body>

<header class="site-header">
  <div class="logo"><span class="dot"></span><span class="brand-name">Hulls for Heroes</span></div>
  <div class="call-box">
    <div class="icon"><svg width="30" height="30" viewBox="0 0 24 24"><path fill="#fff" d="M6.6 10.8a15.1 15.1 0 0 0 6.6 6.6l2.2-2.2c.3-.3.7-.4 1-.2 1.1.4 2.3.6 3.6.6.6 0 1 .4 1 1V20c0 .6-.4 1-1 1A17 17 0 0 1 3 4c0-.6.4-1 1-1h3.5c.6 0 1 .4 1 1 0 1.3.2 2.5.6 3.6.1.3 0 .7-.2 1z"/></svg></div>
    <div><div class="label">Call Today to Donate</div><div class="phone">1-800-555-0142</div><div class="hours">Live Operators Available · 7 Days a Week</div></div>
  </div>
</header>

<nav class="main-nav">
  <ul><li><a href="#how">How to Donate</a></li><li><a href="#why">Why Donate</a></li><li><a href="#faq">FAQ</a></li><li><a href="#about">About</a></li></ul>
  <div class="nav-cta">Donate Your Boats Online</div>
</nav>

<section class="hero">
  <div class="photo" role="img" aria-label="Soldier in camouflage holding a child with a small flag, boats moored in a marina behind"></div>
  <form class="donate-form">
    <h2>Full Tax Deduction – Running or Not</h2>
    <div class="form-row"><span class="field">First Name</span><span class="field">Last Name</span></div>
    <div class="form-row"><span class="field">Daytime Phone</span><span class="field">Email</span></div>
    <div class="form-row"><span class="field">Pickup Address</span></div>
    <div class="form-row"><span class="field">Pickup City</span></div>
    <div class="form-row"><span class="field">Pickup State ▾</span><span class="field">Zip Code</span></div>
    <div class="form-row"><span class="field">Vessel Year ▾</span><span class="field">Vessel Make ▾</span></div>
    <div class="form-row"><span class="field">Vessel Model</span></div>
    <span class="btn-donate">Donate Now</span>
  </form>
</section>

<section class="banner">
  <div class="headline"><span class="l1">Donate Your Boats to</span><span class="l2">Veterans</span><span class="l3">Make a Difference</span></div>
  <div class="perks">
    <div class="perk"><div class="ring"><svg width="26" height="26" viewBox="0 0 24 24"><path d="M4 12l5 5 11-11" stroke="#fff" stroke-width="2.5" fill="none"/></svg></div>Tax Write-off</div>
    <div class="perk"><div class="ring"><svg width="28" height="20" viewBox="0 0 28 20"><path d="M2 12h22l-4 6H6z M8 12V4h8l4 8" stroke="#fff" stroke-width="2" fill="none"/></svg></div>Free towing, running or not</div>
    <div class="perk"><div class="ring"><svg width="24" height="24" viewBox="0 0 24 24"><rect x="5" y="3" width="14" height="18" stroke="#fff" stroke-width="2" fill="none"/><path d="M8 8h8M8 12h8M8 16h5" stroke="#fff" stroke-width="2"/></svg></div>IRS Non-profit 501(c)3 charity</div>
    <div class="perk"><div class="ring"><svg width="24" height="24" viewBox="0 0 24 24"><rect x="4" y="3" width="16" height="18" stroke="#fff" stroke-width="2" fill="none"/><path d="M8 12l3 3 5-6" stroke="#fff" stroke-width="2" fill="none"/></svg></div>We take care of all paperwork</div>
  </div>
</section>

<section class="how" id="how">
  <h2 class="section-title">How to <span class="accent">Donate</span></h2>
  <div class="rule"></div>
  <div class="steps">
    <div class="step">
      <svg class="icon" viewBox="0 0 54 54"><rect x="6" y="10" width="30" height="34" fill="var(--navy)"/><path d="M12 20h18M12 27h18M12 34h12" stroke="#fff" stroke-width="3"/><circle cx="42" cy="38" r="9" fill="var(--red)"/></svg>
      <div><h3>Call us at 1-800-555-0142 or fill out the online form</h3><p>Donating your boat is easy and donation is accepted nationwide.</p></div>
    </div>
    <div class="step">
      <svg class="icon" viewBox="0 0 54 54"><path d="M4 32h46l-8 10H12z" fill="var(--red)"/><path d="M14 32V18h18l8 14" fill="var(--navy)"/></svg>
      <div><h3>We pick up the boat</h3><p>Your boat is scheduled and we will arrange to pick up your boat when it is most convenient for you.</p></div>
    </div>
    <div class="step">
      <svg class="icon" viewBox="0 0 54 54"><rect x="8" y="6" width="28" height="38" fill="none" stroke="var(--navy)" stroke-width="3"/><path d="M14 16h16M14 24h16M14 32h10" stroke="var(--navy)" stroke-width="3"/><circle cx="40" cy="40" r="10" fill="var(--red)"/></svg>
      <div><h3>Tax write-off</h3><p>Once the boat donation is complete, you will receive your tax deductible boat donation receipt.</p></div>
    </div>
  </div>
</section>

<section class="why" id="why">
  <h2 class="section-title">Why Donate Your Boats to Us</h2>
  <svg class="ring-wrap" viewBox="0 0 420 420">
    <circle cx="210" cy="210" r="170" fill="var(--navy-deep)" stroke="#fff" stroke-width="3"/>
    <g fill="var(--red)" stroke="#fff" stroke-width="3">
      <circle cx="60" cy="110" r="30"/><circle cx="40" cy="210" r="30"/><circle cx="60" cy="310" r="30"/>
      <circle cx="360" cy="110" r="30"/><circle cx="380" cy="210" r="30"/><circle cx="360" cy="310" r="30"/>
    </g>
    <g stroke="#fff" stroke-width="2.5" fill="none">
      <path d="M47 114h26l-4 6H51z"/><path d="M30 210l6 6 12-12"/><rect x="50" y="300" width="20" height="20"/>
      <circle cx="360" cy="110" r="10"/><path d="M370 204v12h10"/><path d="M350 310h20M360 300v20"/>
    </g>
  </svg>
  <div class="center-name brand-name">Hulls for Heroes</div>
  <div class="feature left" style="left:40px;top:225px"><h3>Free Local Towing</h3>We will pick up your boat donation, running or not, when it's most convenient for you.</div>
  <div class="feature left" style="left:20px;top:325px"><h3>Income Tax Deduction</h3>We mail your tax receipt so you can claim the highest allowable tax deduction.</div>
  <div class="feature left" style="left:40px;top:425px"><h3>No Paperwork Hassles</h3>We handle title transfer and all the forms, simple and stress free.</div>
  <div class="feature" style="left:830px;top:225px"><h3>A+ Rated &amp; IRS 501(c)3 Approved</h3>A trusted charity with a proven record of service.</div>
  <div class="feature" style="left:850px;top:325px"><h3>Schedule a Free Pickup</h3>Our team will contact you within one day to arrange a pickup time.</div>
  <div class="feature" style="left:830px;top:425px"><h3>Boat donations help fund programs</h3>Your gift supports local veteran services and family aid programs.</div>
</section>

<section class="faq" id="faq">
  <h2 class="section-title">Frequently Asked <span class="accent">Questions</span></h2>
  <div class="faq-list">
    <div class="faq-item"><span>What types of boats can be donated?</span><span>›</span></div>
    <div class="faq-item open"><div class="q"><span>What paperwork do I need to donate my boat?</span><span>⌄</span></div>
      <p>All you need is a title, if one was issued. We will request some general information from you at the time of donation such as the year, make and model of the boat, as well as its general mechanical condition. We accept all boats, running or not running.</p></div>
    <div class="faq-item"><span>Is my donated boat tax-deductible?</span><span>›</span></div>
    <div class="faq-item"><span>What if the boat is not registered in my name?</span><span>›</span></div>
    <div class="faq-item"><span>How much will I receive as a tax deduction for my boat?</span><span>›</span></div>
    <div class="faq-item"><span>When will I receive my tax receipt?</span><span>›</span></div>
    <div class="faq-item"><span>How do I schedule a pick up?</span><span>›</span></div>
  </div>
  <div class="photo" role="img" aria-label="Silhouettes of soldiers raising a flag against a warm sunset sky"></div>
</section>

<footer class="site-footer" id="about">
  <div class="footer-brand"><span class="brand-name">Hulls for Heroes</span></div>
  <div class="footer-cols">
    <div class="footer-col" style="width:240px">
      <h4>About Hulls for Heroes</h4>
      <p>We turn donated boats into real support for veterans and their families. Every vessel helps fund housing, job training and care programs across the country. Thank you for giving back to those who served.</p>
    </div>
    <div class="footer-col" style="width:140px">
      <h4>Navigation</h4>
      <ul><li>How to Donate</li><li>Why Donate</li><li>FAQ</li><li>About Us</li><li>Contact</li></ul>
    </div>
    <div class="footer-col" style="width:170px">
      <h4>Safe &amp; Secure</h4>
      <div class="badge"></div><div class="badge"></div><div class="badge round"></div>
    </div>
  </div>
  <div class="footer-call call-box">
    <div class="icon"><svg width="30" height="30" viewBox="0 0 24 24"><path fill="#fff" d="M6.6 10.8a15.1 15.1 0 0 0 6.6 6.6l2.2-2.2c.3-.3.7-.4 1-.2 1.1.4 2.3.6 3.6.6.6 0 1 .4 1 1V20c0 .6-.4 1-1 1A17 17 0 0 1 3 4c0-.6.4-1 1-1h3.5c.6 0 1 .4 1 1 0 1.3.2 2.5.6 3.6.1.3 0 .7-.2 1z"/></svg></div>
    <div><div class="label">Call Today to Donate</div><div class="phone">1-800-555-0142</div><div class="hours">Live Operators Available · 7 Days a Week</div></div>
  </div>
</footer>
<div class="copyright">Copyright © 2017 Hulls for Heroes. Privacy Policy | Terms &amp; Conditions. All rights reserved.</div>

</body>
</html>
```